Logo with Stationery Design Project-

The company is an on-line service for assisting the people that are in a foreclosure situation with their homes. We are presently building the site on WebMarlin with Wordpress.

The best option to save a home in the USA at the end of the line with the banks is to file for bankruptcy Chapter 7 or Chapter 13. We work with homeowners and attorneys to prepare the financial package for the attorneys to negotiate with the banks after filing for bankruptcy. We also sell a binder on-line which is called the northgate renewal set and the web site is: www.northgaterenewalset.example
We need a logo and stationnary to communicate the message of advisors in the field of financial strategies when it comes to the foreclosure and bankruptcy process. This stationnary will be printed on high quality paper with the business cards being on 100 stock which is high quality in the USA.

We would like to see the logo to use the Navy blue and Aqua Green colors. The final desing should communicate the financial knowledge and promise of a light at the end of the tunnell.

The card should use both sides with the back side being the logo and the web site address that links with the front of the card. Letterhead and envelopes should be serious but sexy!

A challenge that I am sure someone is up to........

Target Market(s)

12 million people that are in foreclosure in the USA and all of the law firms that deal with foreclosure and bankruptcies in the USA all 50 states

Industry/Entity Type

Financial

Requirements
Must have
• Colors are important = Navy blue and Aqua green

```html
<!DOCTYPE html>
<html lang="en">
<head>
<meta charset="utf-8">
<title>Northgate Renewal – Stationery</title>
<link rel="stylesheet" href="https://fonts.googleapis.com/css2?family=Montserrat:wght@400;500;700&display=swap">
<style>
  :root{
    --teal:#16a193;
    --teal-soft:#8fd3cb;
    --navy:#1d2b4f;
    --paper:#ffffff;
    --ink:#4a4f58;
    --rule:#b9bec6;
    --stage:#3b3c3f;
    --font:"Montserrat", Arial, sans-serif;
  }
  *{box-sizing:border-box;margin:0;padding:0}
  html,body{width:1200px;height:999px;overflow:hidden}
  body{background:var(--stage);font-family:var(--font);color:var(--ink);position:relative}
  .piece{position:absolute;background:var(--paper);box-shadow:0 6px 18px rgba(0,0,0,.35)}

  /* brand lockup */
  .brand{display:flex;align-items:center;gap:.45em;font-weight:700;color:var(--navy);letter-spacing:.02em;text-transform:uppercase;white-space:nowrap}
  .brand-mark{width:.9em;height:.9em;background:currentColor;flex:none}
  .brand--light{color:var(--paper)}

  .url{font-weight:500;color:var(--navy);white-space:nowrap}
  .url em{font-style:normal;color:var(--teal)}

  /* folder */
  .folder{left:26px;top:77px;width:327px;height:506px;background:var(--teal)}
  .folder .brand{position:absolute;left:0;right:0;top:296px;justify-content:center;font-size:18px}
  .folder .url{position:absolute;left:0;right:0;bottom:26px;text-align:center;font-size:12px;color:var(--paper)}
  .folder .url em{color:var(--navy)}

  /* letterhead */
  .letterhead{left:375px;top:77px;width:325px;height:506px;padding:20px 22px;font-size:6.2px;line-height:1.55}
  .letterhead .brand{font-size:11px}
  .sender{margin-top:8px;color:var(--navy);font-weight:500}
  .recipient{position:absolute;right:26px;top:96px;text-align:left}
  .letter-body{margin-top:42px}
  .letter-body p{margin-bottom:7px}
  .signoff{margin-top:12px}
  .letterhead .url{position:absolute;left:0;right:0;bottom:18px;text-align:center;font-size:7.5px}

  /* envelopes */
  .envelope{left:723px;width:453px;overflow:hidden}
  .envelope--front{top:77px;height:249px}
  .envelope--back{top:340px;height:243px}
  .envelope svg{position:absolute;left:0;top:0;width:100%}
  .envelope--front .brand{position:absolute;left:14px;top:92px;font-size:11px}
  .envelope--front .sender{position:absolute;left:14px;top:114px;font-size:7px;line-height:1.55;margin:0}

  /* business cards */
  .card{top:626px;width:480px;height:271px;border-radius:16px}
  .card--front{left:77px}
  .card--back{left:629px}
  .card--front .brand{position:absolute;left:0;right:0;top:150px;justify-content:center;font-size:21px}
  .card .url{position:absolute;left:0;right:0;bottom:20px;text-align:center;font-size:14px}
  .card--back .brand{position:absolute;left:40px;top:160px;font-size:11.5px}
  .divider{position:absolute;left:255px;top:82px;width:1px;height:110px;background:var(--rule)}
  .contact{position:absolute;left:272px;top:84px;font-size:10px;line-height:1.45;color:var(--navy)}
  .contact .name{font-size:16px;font-weight:500;color:var(--teal);line-height:1.1}
  .contact .role{font-size:10px;color:var(--ink);margin-bottom:10px}
  .contact .addr{font-weight:500}
  .contact ul{list-style:none;margin-top:2px}
  .contact li{display:flex;align-items:center;gap:6px}
  .contact svg{width:10px;height:10px;fill:var(--navy);flex:none}
</style>
</head>
<body>

<section class="piece folder" aria-label="Presentation folder">
  <div class="brand brand--light"><span class="brand-mark"></span>Northgate Renewal</div>
  <p class="url">www.<em>northgaterenewalset</em>.example</p>
</section>

<section class="piece letterhead" aria-label="Letterhead">
  <div class="brand"><span class="brand-mark"></span>Northgate Renewal</div>
  <p class="sender">48 Harbor Lane,<br>Albany, NY<br>+ 00 000 0000<br>+ 00 000 0000<br>hello@northgate.example</p>
  <p class="recipient">Jane Holloway<br>14 Elm Road<br>Hartford, CT</p>
  <div class="letter-body">
    <p>Dear Jane Holloway,</p>
    <p>Thank you for reaching out about your home. Our team prepares the full financial package your attorney needs to negotiate with the bank after filing.</p>
    <p>We review income, debts and assets, then organise every statement into one clear binder so nothing is missed during the Chapter 7 or Chapter 13 process.</p>
    <p>Each step is explained in plain language, with checklists and deadlines you can follow at your own pace from any device.</p>
    <p>Please call or email us with any questions. We look forward to helping you keep your home.</p>
    <p class="signoff">Yours Sincerely,<br>Daniel Whitcombe</p>
  </div>
  <p class="url">www.<em>northgaterenewalset</em>.example</p>
</section>

<section class="piece envelope envelope--front" aria-label="Envelope, front">
  <svg viewBox="0 0 453 70" height="70" aria-hidden="true">
    <polygon points="0,0 453,0 453,8 226,58 0,8" fill="var(--teal)"/>
  </svg>
  <div class="brand"><span class="brand-mark"></span>Northgate Renewal</div>
  <p class="sender">48 Harbor Lane,<br>Albany, NY<br>+ 00 000 0000<br>+ 00 000 0000<br>hello@northgate.example</p>
</section>

<section class="piece envelope envelope--back" aria-label="Envelope, back">
  <svg viewBox="0 0 453 90" height="90" aria-hidden="true">
    <polygon points="0,0 453,0 453,14 226,82 0,14" fill="var(--teal)"/>
  </svg>
</section>

<section class="piece card card--front" aria-label="Business card, logo side">
  <div class="brand"><span class="brand-mark"></span>Northgate Renewal</div>
  <p class="url">www.<em>northgaterenewalset</em>.example</p>
</section>

<section class="piece card card--back" aria-label="Business card, contact side">
  <div class="brand"><span class="brand-mark"></span>Northgate Renewal</div>
  <span class="divider"></span>
  <div class="contact">
    <p class="name">Daniel Whitcombe</p>
    <p class="role">Title</p>
    <p class="addr">48 Harbor Lane,<br>Albany, NY</p>
    <ul>
      <li><svg viewBox="0 0 10 10"><path d="M2 0h2l1 2.5-1.3 1a6 6 0 0 0 2.8 2.8l1-1.3L10 6v2a2 2 0 0 1-2 2A8 8 0 0 1 0 2a2 2 0 0 1 2-2z"/></svg>+ 00 000 0000</li>
      <li><svg viewBox="0 0 10 10"><path d="M1 2h8v6H1z"/></svg>+ 00 000 0000</li>
      <li><svg viewBox="0 0 10 10"><path d="M0 2h10v6H0zM0 2l5 3.5L10 2" stroke="#fff" stroke-width=".8"/></svg>hello@northgate.example</li>
    </ul>
  </div>
  <p class="url">www.<em>northgaterenewalset</em>.example</p>
</section>

</body>
</html>
```